Jewelers Website

This is for the DESIGN ONLY.
I am a software programmer and will be doing the development.
New website design for
www.lunacrestgems.com.au
Need a fresh new look for an online only jewellery business who produce their jewellery by hand. I would like it designed in a parallax style. Feel free to recommend fonts to use for the site. This is an Australian based company located in NSW so shots of sites in NSW might make nice background images.
http://vornaplex.me/demo/#theme=parallax
To contain the below sections
About Us
Contact Us
Gallery
Testimonials
Diamond Types
The colour scheme is to be Black / White and Silver.
With the Parallax style there will be moving sections and images for added impact.
Target Market(s)
Young Adults mainly engagement jewellery

```html
<!DOCTYPE html>
<html lang="en">
<head>
<meta charset="utf-8">
<title>Lunacrest Gems — Diamond Engagement Rings Australia</title>
<link href="https://fonts.googleapis.com/css2?family=Open+Sans:wght@300;400;600&display=swap" rel="stylesheet">
<style>
:root{
  --black:#000;
  --ink:#111;
  --white:#fff;
  --silver:#c9c9c9;
  --mist:#8d8d8d;
  --field:#e9e9e9;
  --footer:#ececec;
  --line:#d5d5d5;
  --text-grey:#6b6b6b;
  --navy:#0d1a3a;
}
*{margin:0;padding:0;box-sizing:border-box}
html,body{width:1200px;height:4045px;overflow:hidden}
body{font-family:'Open Sans',Arial,sans-serif;color:var(--ink);background:var(--white);position:relative}
section,header,footer{position:absolute;left:0;width:1200px}

/* Hero */
.hero{top:0;height:742px;background:var(--black)}
.hero-image{position:absolute;inset:0;background:
  radial-gradient(ellipse 520px 260px at 430px 330px,#cfcfcf 0%,#7c7c7c 35%,#2a2a2a 70%,transparent 100%),
  radial-gradient(ellipse 300px 200px at 820px 250px,#9a9a9a 0%,#333 60%,transparent 100%),
  linear-gradient(180deg,#1c1c1c 0%,#3a3a3a 45%,#0d0d0d 100%)}
.site-nav{position:absolute;top:0;left:0;width:100%;height:82px}
.logo{position:absolute;left:97px;top:16px;color:var(--white);font-size:25px;font-weight:400;line-height:27px;letter-spacing:1px}
.menu{position:absolute;left:478px;top:30px;display:flex;gap:36px;list-style:none}
.menu li{font-size:13px;color:#a5a5a5;letter-spacing:.3px;padding-bottom:22px}
.menu li.active{color:var(--white);font-weight:600;border-bottom:2px solid var(--white)}
.hero-arrow{position:absolute;top:385px}
.hero-arrow.left{left:40px}
.hero-arrow.right{right:40px}
.hero-title{position:absolute;top:530px;width:100%;text-align:center;color:var(--white);font-size:30px;font-weight:400;letter-spacing:1px}
.hero-btn{position:absolute;top:593px;left:526px;width:148px;height:43px;border:1px solid #9a9a9a;color:var(--white);font-size:13px;display:flex;align-items:center;justify-content:center;letter-spacing:.5px}
.dots{position:absolute;top:692px;left:0;width:100%;display:flex;justify-content:center;gap:11px}
.dots span{width:11px;height:11px;border-radius:50%;background:#777}
.dots span.on{background:var(--white)}

/* About */
.about{top:742px;height:722px;background:radial-gradient(ellipse 700px 380px at 600px 330px,#9b9b9b 0%,#6f6f6f 45%,#464646 100%);color:var(--white);text-align:center}
.about h2{position:absolute;width:100%;font-size:28px;font-weight:400}
.about p{position:absolute;left:160px;width:880px;font-size:13px;line-height:25px}
.about .h-one{top:130px}
.about .p-one{top:183px}
.about .h-two{top:302px}
.about .p-two{top:350px}

/* Gallery & testimonials */
.gallery{top:1464px;height:753px;background:var(--black)}
.testimonials{top:2217px;height:763px}
.testimonials-bg{position:absolute;inset:0;background:linear-gradient(100deg,#0a1230 0%,#17306a 45%,#1a2c5e 65%,#0d1736 100%)}
.portrait-panel{position:absolute;right:0;top:0;width:360px;height:763px;background:linear-gradient(90deg,rgba(20,40,90,0) 0%,#8a6d68 35%,#d6b3a4 70%,#e6c7b8 100%)}
.section-title{position:absolute;top:60px;width:100%;text-align:center;color:var(--white);font-size:28px;font-weight:400}
.tile{position:absolute;width:216px;text-align:center}
.octagon{width:216px;height:216px;clip-path:polygon(29% 0,71% 0,100% 29%,100% 71%,71% 100%,29% 100%,0 71%,0 29%)}
.caption{margin-top:14px;color:var(--white);font-size:13px}
.c1{left:135px}.c2{left:491px}.c3{left:844px}
.r1{top:154px}.r2{top:432px}
.t1{left:135px}.t2{left:393px}.t3{left:651px}
.tr1{top:135px}.tr2{top:418px}
.tone-silver{background:radial-gradient(circle at 45% 40%,#f4f4f4,#9c9c9c 60%,#5a5a5a)}
.tone-warm{background:radial-gradient(circle at 50% 45%,#c99a6d,#6a4a2e 65%,#1a120c)}
.tone-white{background:radial-gradient(circle at 50% 50%,#d8d8d8,#fafafa 60%)}
.tone-hand{background:radial-gradient(circle at 50% 50%,#caa48e,#8f6a58 60%,#4b3a33)}
.tone-blue{background:radial-gradient(circle at 55% 50%,#2f57b0,#0d1a4a 60%,#050812)}
.tone-dark{background:radial-gradient(circle at 50% 50%,#b8b8b8,#3d3d3d 55%,#0a0a0a)}
.tone-couple{background:linear-gradient(160deg,#a6bccc,#e8e4df 55%,#3d3d42)}
.tone-outdoor{background:linear-gradient(180deg,#dfe8cf,#7f9a6a 55%,#46603c)}
.tone-wedding{background:linear-gradient(180deg,#b59a6c,#e9e3d6 55%,#2b2620)}
.tone-sun{background:radial-gradient(circle at 60% 35%,#fff4d6,#e7c49a 55%,#a8775a)}
.tone-pale{background:radial-gradient(circle at 50% 50%,#f2efeb,#cfc7bf 70%)}

/* Contact */
.contact{top:2980px;height:769px;background:var(--white)}
.contact h2{position:absolute;left:135px;top:135px;font-size:27px;font-weight:300;color:#555;letter-spacing:.5px}
.contact .intro{position:absolute;left:135px;top:185px;width:480px;font-size:12.5px;line-height:21px;color:var(--text-grey)}
.field{position:absolute;left:135px;width:488px;background:var(--field);color:#8a8a8a;font-size:12px;padding:12px 20px}
.f-name{top:258px;height:43px}
.f-email{top:331px;height:43px}
.f-msg{top:404px;height:135px}
.send{position:absolute;left:458px;top:553px;width:165px;height:49px;border:1px solid #777;font-size:12px;color:#555;display:flex;align-items:center;justify-content:center;letter-spacing:.5px}
.divider{position:absolute;left:673px;top:160px;width:1px;height:580px;background:var(--line)}
.fan-box{position:absolute;left:715px;top:165px;width:345px}
.fan-head{display:flex;gap:12px;align-items:flex-start}
.fan-square{width:52px;height:52px;background:#3b5998}
.fan-head h3{font-size:23px;font-weight:400;color:#333;line-height:27px}
.fan-head small{display:block;font-size:12px;color:#666}
.fan-widget{margin-top:22px;border:1px solid var(--line);padding:10px}
.fan-widget .name{font-size:12px;font-weight:600;color:#3b5998;display:flex;gap:8px;align-items:center}
.fan-widget .name i{width:40px;height:16px;background:#4b67a1;display:inline-block}
.fan-widget .count{font-size:10px;color:#777;margin:14px 0 8px}
.fan-grid{height:178px;background:linear-gradient(135deg,#c9b6a8,#7e7f86 40%,#b7aaa0 70%,#6f6863)}
.fan-widget .foot{font-size:9px;color:#999;margin-top:10px}

/* Footer */
.site-footer{top:3749px;height:296px;background:var(--footer)}
.f-col{position:absolute;top:46px}
.f-col h4{font-size:13px;font-weight:600;color:#222;letter-spacing:.3px}
.f-col ul{list-style:none;margin-top:8px}
.f-col li{font-size:10.5px;line-height:13px;color:#666}
.col-menu{left:135px}
.col-types{left:278px}
.col-news{left:480px}
.col-social{left:898px}
.subscribe{display:flex;margin-top:10px}
.subscribe .in{width:235px;height:38px;background:var(--white);font-size:11px;color:#999;padding:11px 12px;font-style:italic}
.subscribe .go{width:97px;height:38px;background:var(--black);color:var(--white);font-size:14px;display:flex;align-items:center;justify-content:center}
.social{display:flex;gap:17px;margin-top:18px}
.social span{width:27px;height:27px;border-radius:50%}
.s1{background:#2aa9e0}.s2{background:#3b5998}.s3{background:#d9473a}.s4{background:#1a7ab8}
.foot-rule{position:absolute;left:135px;top:229px;width:1025px;height:1px;background:var(--line)}
.copyright{position:absolute;right:40px;top:248px;font-size:10px;color:#777;letter-spacing:.3px}
</style>
</head>
<body>

<header class="hero">
  <div class="hero-image" role="img" aria-label="Close-up photograph of loose brilliant-cut diamonds on dark fabric"></div>
  <nav class="site-nav">
    <div class="logo">LUNACREST<br>GEMS</div>
    <ul class="menu">
      <li class="active">HOME</li>
      <li>ABOUT US</li>
      <li>CONTACT US</li>
      <li>GALLERY</li>
      <li>TESTIMONIALS</li>
      <li>DIAMOND TYPES</li>
    </ul>
  </nav>
  <svg class="hero-arrow left" width="24" height="44" viewBox="0 0 24 44"><polyline points="22,2 2,22 22,42" fill="none" stroke="#bbb" stroke-width="2"/></svg>
  <svg class="hero-arrow right" width="24" height="44" viewBox="0 0 24 44"><polyline points="2,2 22,22 2,42" fill="none" stroke="#bbb" stroke-width="2"/></svg>
  <h1 class="hero-title">DIAMOND ENGAGEMENT RINGS AUSTRALIA</h1>
  <div class="hero-btn">KNOW MORE</div>
  <div class="dots"><span class="on"></span><span></span><span></span><span></span></div>
</header>

<section class="about">
  <h2 class="h-one">Diamond Engagement Rings &amp; Jewellery</h2>
  <p class="p-one">At Lunacrest Gems we specialise in creating beautiful jewellery and diamond engagement rings using the very best diamonds, gemstones and precious metals from Australia and around the world.</p>
  <h2 class="h-two">Diamond engagement rings Australia</h2>
  <p class="p-two">We specialise in the design and creation of one-off pieces of exceptional quality that cannot be found elsewhere. Our team of highly skilled jewellers based in Sydney are committed to making sure that each ring we produce is unique and only the finest materials are used so you can be sure that whatever you order will be truly special. Many internet jewellery stores stock affordable pieces and a select few offer items of breathtaking beauty. However, few are capable of offering both. Whether you prefer vintage designs or modern bands set with round, square and emerald cut stones, you will not find better diamond engagement rings online. We have made it our mission to supply the best pieces at highly competitive prices and because we have eliminated the expenses that are associated with owning flagship stores in prime city-centre locations, we are able to keep running costs to a minimum.</p>
</section>

<section class="gallery">
  <h2 class="section-title">Diamond Gallery</h2>
  <div class="tile c1 r1"><div class="octagon tone-silver" role="img" aria-label="Large faceted diamond close-up"></div><p class="caption">Liam &amp; Sienna</p></div>
  <div class="tile c2 r1"><div class="octagon tone-warm" role="img" aria-label="Model wearing diamond jewellery"></div><p class="caption">Liam &amp; Sienna</p></div>
  <div class="tile c3 r1"><div class="octagon tone-white" role="img" aria-label="Halo diamond engagement ring on white"></div><p class="caption">Liam &amp; Sienna</p></div>
  <div class="tile c1 r2"><div class="octagon tone-hand" role="img" aria-label="Hand wearing a diamond ring"></div><p class="caption">Liam &amp; Sienna</p></div>
  <div class="tile c2 r2"><div class="octagon tone-blue" role="img" aria-label="Sapphire and diamond jewellery on blue"></div><p class="caption">Liam &amp; Sienna</p></div>
  <div class="tile c3 r2"><div class="octagon tone-dark" role="img" aria-label="Diamond rings arranged on black"></div><p class="caption">Liam &amp; Sienna</p></div>
</section>

<section class="testimonials">
  <div class="testimonials-bg" role="img" aria-label="Deep blue backdrop photograph"></div>
  <div class="portrait-panel" role="img" aria-label="Close-up beauty portrait wearing a blue gemstone earring"></div>
  <h2 class="section-title">Stories &amp; Testimonials</h2>
  <div class="tile t1 tr1"><div class="octagon tone-warm" role="img" aria-label="Customer portrait with jewellery"></div><p class="caption">Liam &amp; Sienna</p></div>
  <div class="tile t2 tr1"><div class="octagon tone-couple" role="img" aria-label="Wedding couple beside a car"></div><p class="caption">Liam &amp; Sienna</p></div>
  <div class="tile t3 tr1"><div class="octagon tone-outdoor" role="img" aria-label="Couple outdoors on their wedding day"></div><p class="caption">Liam &amp; Sienna</p></div>
  <div class="tile t1 tr2"><div class="octagon tone-pale" role="img" aria-label="Bride's hands showing an engagement ring"></div><p class="caption">Liam &amp; Sienna</p></div>
  <div class="tile t2 tr2"><div class="octagon tone-wedding" role="img" aria-label="Wedding party group photograph"></div><p class="caption">Liam &amp; Sienna</p></div>
  <div class="tile t3 tr2"><div class="octagon tone-sun" role="img" aria-label="Couple embracing in sunlight"></div><p class="caption">Liam &amp; Sienna</p></div>
</section>

<section class="contact">
  <h2>CONTACT US</h2>
  <p class="intro">Praesent varius elit pellentesque accu molestie condimentum. Suspendisse potenti. Fusce a pharetra arcu, eget aliquam leo.</p>
  <div class="field f-name">Whats your name</div>
  <div class="field f-email">Email address</div>
  <div class="field f-msg">Message</div>
  <div class="send">SEND MAIL</div>
  <div class="divider"></div>
  <div class="fan-box">
    <div class="fan-head">
      <span class="fan-square"></span>
      <div><h3>Get Fan Exclusives</h3><small>Join our fan page</small></div>
    </div>
    <div class="fan-widget">
      <div class="name"><i></i>Lunacrest Gems</div>
      <p class="count">205,327 people like Lunacrest Gems</p>
      <div class="fan-grid" role="img" aria-label="Grid of fan profile photographs"></div>
      <p class="foot">Our social page plugin</p>
    </div>
  </div>
</section>

<footer class="site-footer">
  <div class="f-col col-menu">
    <h4>MENU</h4>
    <ul><li>HOME</li><li>ABOUT US</li><li>CONTACT US</li><li>GALLERY</li><li>TESTIMONIALS</li><li>DIAMOND TYPES</li></ul>
  </div>
  <div class="f-col col-types">
    <h4>DIAMOND TYPES</h4>
    <ul><li>ROUND BRILLIANT</li><li>PRINCESS CUT</li><li>EMERALD CUT</li><li>OVAL CUT</li><li>CUSHION CUT</li><li>RADIANT CUT</li></ul>
  </div>
  <div class="f-col col-news">
    <h4>SUBSCRIBE NEWSLETTER</h4>
    <div class="subscribe"><div class="in">enter your mail address</div><div class="go">submit</div></div>
  </div>
  <div class="f-col col-social">
    <h4>FIND US ON</h4>
    <div class="social"><span class="s1"></span><span class="s2"></span><span class="s3"></span><span class="s4"></span></div>
  </div>
  <div class="foot-rule"></div>
  <p class="copyright">COPYRIGHT 2014 LUNACRESTGEMS. ALL RIGHTS ARE RESERVED | GENERAL TERMS AND CONDITIONS</p>
</footer>

</body>
</html>
```